8x8 Social Media Ad - Brant Summit Expo

Attention Real Estate Agents
Please join us for our
Quarterly Real Estate Training Expo
The 2nd Saturday of February, May, August and November
Our Next Training Expo is _________________________________
From 9 am to 1 pm
at
Halvorne Suites Millbrook Court
4817 Copper Willow Lane, Dunmere, MD 20588
Scheduled Speakers
9:00 am - Marcus Pellington - Orientation
9:30 am - Derrin Oakfield - Multiple Income Streams / Crest Program
10:00 am - Talia Brennick - Marketing though Social Media
10:45 am - Rex Dunmore - Generating Business through Ru-Plaza
11:30 am - Kemi Adeyoro - Real Estate Investing
12:15 pm - Gregor Tamsey - (Main Speaker) Training Topic TBA
For more information call Marcus Pellington at (240) 555-0183 or email mpellington@brantsummithomes.example

```html
<!DOCTYPE html>
<html lang="en">
<head>
<meta charset="utf-8">
<title>Brant Summit Expo – Quarterly Training Expo</title>
<link href="https://fonts.googleapis.com/css2?family=Anton&family=Poppins:wght@400;500;600;700&display=swap" rel="stylesheet">
<style>
:root{
  --teal:#0a8a9a;
  --dark:#2c2c2c;
  --ink:#151515;
  --white:#ffffff;
  --photo-a:#d9dde0;
  --photo-b:#aab3b9;
}
*{margin:0;padding:0;box-sizing:border-box}
html,body{width:1200px;height:1200px;overflow:hidden;background:var(--white)}
.ad{position:relative;width:1200px;height:1200px;font-family:"Poppins",sans-serif;color:var(--ink);overflow:hidden}
.backdrop{position:absolute;inset:0}
.abs{position:absolute;white-space:nowrap}
.brand{left:40px;top:70px;width:300px;display:flex;align-items:center;gap:12px;font-weight:700;font-size:26px;line-height:1.1;color:var(--teal)}
.brand-dot{width:22px;height:22px;border-radius:50%;background:var(--teal);flex:none}
.attention{left:440px;top:43px;width:485px;text-align:center;font-weight:700;font-size:85px;line-height:1;color:var(--white);letter-spacing:1px}
.agents-box{left:440px;top:131px;width:485px;height:59px;border:2px solid var(--white);display:flex;align-items:center;justify-content:center;font-weight:700;font-size:40px;color:var(--white)}
.megaphone{left:960px;top:55px;width:195px;height:130px;border-radius:20px;background:rgba(255,255,255,.28)}
.when-1{left:0;width:1200px;top:428px;text-align:center;font-weight:700;font-size:58px;line-height:1}
.when-1 sup{font-size:30px;vertical-align:24px}
.when-2{left:0;width:1200px;top:482px;text-align:center;font-weight:700;font-size:56px;line-height:1;color:var(--teal)}
.next-label{left:100px;top:574px;font-weight:600;font-size:27px}
.next-field{left:479px;top:572px;width:616px;height:36px;border:1.5px solid var(--ink);border-radius:18px;background:#fafafa}
.hours{left:74px;top:642px;width:404px;height:47px;border-radius:24px;background:var(--teal);color:var(--white);font-weight:700;font-size:30px;display:flex;align-items:center;justify-content:center}
.pin{left:521px;top:640px;width:36px;height:48px}
.venue-name{left:575px;top:641px;font-weight:600;font-size:18px;color:var(--white)}
.venue-addr{left:575px;top:665px;font-weight:400;font-size:21px;color:var(--white);letter-spacing:.5px}
.photo{position:absolute;width:152px;height:105px;border:2px solid var(--teal);border-radius:22px;background:linear-gradient(160deg,var(--photo-a),var(--photo-b))}
.speaker-name{position:absolute;font-weight:600;font-size:21px;line-height:1.1;white-space:nowrap}
.speaker-topic{position:absolute;font-weight:400;font-size:19px;line-height:1.3;white-space:nowrap}
.main-tag{font-weight:400;font-size:16px;margin-left:12px}
.time{position:absolute;width:119px;height:28px;border-radius:14px;background:var(--teal);color:var(--white);font-weight:600;font-size:19px;display:flex;align-items:center;justify-content:center}
.more{left:51px;top:1093px;font-size:21px;color:var(--white)}
.call{left:51px;top:1118px;font-weight:700;font-size:30px;color:var(--white);display:flex;align-items:center;gap:12px}
.call .who{color:var(--teal)}
.icon{display:inline-block;flex:none}
.contact{top:1122px;display:flex;align-items:center;gap:8px;color:var(--white);font-weight:600}
.phone{left:540px;font-size:20px}
.or{left:727px;top:1127px;font-size:18px;color:var(--teal)}
.email{left:760px;font-size:15.5px}
</style>
</head>
<body>
<div class="ad">
  <svg class="backdrop" width="1200" height="1200" viewBox="0 0 1200 1200">
    <polygon points="415,0 1200,0 1200,419 0,419 0,186 301,186" fill="var(--teal)"/>
    <polygon points="1200,334 1200,419 1131,419" fill="var(--white)"/>
    <polygon points="211,223 1057,223 992,330 141,330" fill="var(--white)"/>
    <polygon points="88,335 1127,335 1098,417 56,417" fill="var(--ink)"/>
    <polygon points="1098,324 1145,337 1115,356" fill="var(--ink)"/>
    <text x="223" y="313" font-family="Anton, sans-serif" font-size="80" fill="var(--ink)" textLength="754" lengthAdjust="spacingAndGlyphs">PLEASE JOIN US FOR OUR</text>
    <text x="123" y="401" font-family="Anton, sans-serif" font-size="68" textLength="953" lengthAdjust="spacingAndGlyphs"><tspan fill="var(--white)">QUARTERLY REAL ESTATE </tspan><tspan fill="var(--teal)">TRAINING EXPO</tspan></text>
    <line x1="49" y1="550" x2="1151" y2="550" stroke="var(--ink)" stroke-width="1.5"/>
    <rect x="526" y="546" width="149" height="8" fill="var(--teal)"/>
    <rect x="0" y="626" width="1200" height="78" fill="var(--dark)"/>
    <rect x="0" y="1049" width="1200" height="151" fill="var(--dark)"/>
  </svg>

  <div class="abs brand"><span class="brand-dot"></span><span>Brant Summit<br>Realty Group</span></div>

  <div class="abs attention">ATTENTION</div>
  <div class="abs agents-box">REAL ESTATE AGENTS</div>
  <div class="abs megaphone" role="img" aria-label="Megaphone illustration"></div>

  <div class="abs when-1">THE 2<sup>ND</sup> SATURDAY OF</div>
  <div class="abs when-2">FEBRUARY, MAY, AUGUST &amp; NOVEMBER</div>

  <div class="abs next-label">Our Next Training Expo is</div>
  <div class="abs next-field"></div>

  <div class="abs hours">FROM 9 AM TO 1 PM AT</div>
  <svg class="abs pin" viewBox="0 0 36 48" aria-hidden="true">
    <path d="M18 2a15 15 0 0 0-15 15c0 11 15 27 15 27s15-16 15-27A15 15 0 0 0 18 2z" fill="none" stroke="var(--teal)" stroke-width="4"/>
    <circle cx="18" cy="17" r="5" fill="var(--teal)"/>
  </svg>
  <div class="abs venue-name">HALVORNE SUITES MILLBROOK COURT</div>
  <div class="abs venue-addr">4817 Copper Willow Lane, Dunmere, MD 20588</div>

  <div class="photo" style="left:54px;top:723px" role="img" aria-label="Portrait of speaker Marcus Pellington"></div>
  <div class="speaker-name" style="left:227px;top:732px">MARCUS PELLINGTON</div>
  <div class="speaker-topic" style="left:227px;top:755px">Orientation</div>
  <div class="time" style="left:221px;top:787px">9:00 AM</div>

  <div class="photo" style="left:54px;top:845px" role="img" aria-label="Portrait of speaker Derrin Oakfield"></div>
  <div class="speaker-name" style="left:227px;top:841px">DERRIN OAKFIELD</div>
  <div class="speaker-topic" style="left:227px;top:866px">Multiple Income<br>Streams / Crest Program</div>
  <div class="time" style="left:221px;top:922px">9:30 AM</div>

  <div class="photo" style="left:54px;top:969px" role="img" aria-label="Portrait of speaker Talia Brennick"></div>
  <div class="speaker-name" style="left:227px;top:980px">TALIA BRENNICK</div>
  <div class="speaker-topic" style="left:227px;top:1001px">Marketing through Social Media</div>
  <div class="time" style="left:221px;top:1031px">10:00 AM</div>

  <div class="photo" style="left:593px;top:723px" role="img" aria-label="Portrait of speaker Rex Dunmore"></div>
  <div class="speaker-name" style="left:765px;top:732px">REX DUNMORE</div>
  <div class="speaker-topic" style="left:765px;top:755px">Generating Business through Ru-Plaza</div>
  <div class="time" style="left:765px;top:787px">10:45 AM</div>

  <div class="photo" style="left:593px;top:845px" role="img" aria-label="Portrait of speaker Kemi Adeyoro"></div>
  <div class="speaker-name" style="left:765px;top:855px">KEMI ADEYORO</div>
  <div class="speaker-topic" style="left:765px;top:880px">Real Estate Investing</div>
  <div class="time" style="left:765px;top:921px">11:30 AM</div>

  <div class="photo" style="left:593px;top:969px" role="img" aria-label="Portrait of main speaker Gregor Tamsey"></div>
  <div class="speaker-name" style="left:765px;top:975px">GREGOR TAMSEY<span class="main-tag">(Main Speaker)</span></div>
  <div class="speaker-topic" style="left:765px;top:997px">Training Topic TBA</div>
  <div class="time" style="left:765px;top:1032px">12:15 PM</div>

  <div class="abs more">For more information</div>
  <div class="abs call">CALL
    <svg class="icon" width="28" height="28" viewBox="0 0 28 28" aria-hidden="true"><circle cx="14" cy="14" r="12" fill="none" stroke="var(--teal)" stroke-width="3"/><path d="M10 8c-1 1-1 3 1 6s4 5 6 6l2-2-3-2-1 1c-1-.5-3-2.5-3.5-3.5l1-1-2-3z" fill="var(--teal)"/></svg>
    <span class="who">MARCUS PELLINGTON</span>
  </div>
  <div class="abs contact phone">
    <svg class="icon" width="26" height="26" viewBox="0 0 26 26" aria-hidden="true"><circle cx="13" cy="13" r="12" fill="var(--white)"/><path d="M9 7c-1 1-1 3 1 6s4 5 6 6l2-2-3-2-1 1c-1-.5-3-2.5-3.5-3.5l1-1-2-3z" fill="var(--dark)"/></svg>
    <span>240 555-0183</span>
  </div>
  <div class="abs or">OR</div>
  <div class="abs contact email">
    <svg class="icon" width="26" height="26" viewBox="0 0 26 26" aria-hidden="true"><circle cx="13" cy="13" r="12" fill="var(--white)"/><rect x="7" y="9" width="12" height="9" rx="1" fill="var(--dark)"/><path d="M7 9l6 5 6-5" fill="none" stroke="var(--white)" stroke-width="1.3"/></svg>
    <span>mpellington@brantsummithomes.example</span>
  </div>
</div>
</body>
</html>
```